Pre-Paid Card for Teens needs a design

We are a Fintech company called Toqavel. We will sell prepaid cards for families and teens. Now we need a prepaid card design. Prepaid card should have a orbitpay logo, company logo, 16 card number, expire date. Our webpage is http://www.toqavel-example.com
Target Market(s)
Teenages between 8 - 18 years old
Industry/Entity Type
It Company
Requirements
Must have
- The prepaid card must include toqavel logo, orbitpay debit card logo (I already attached a sample card), 16 digit card number and expire date.
Nice to have
- It should be fun and prestigious for young people.
Should not have
- We don't want that the card has a lots of color

```html
<!DOCTYPE html>
<html lang="en">
<head>
<meta charset="utf-8">
<title>Toqavel Prepaid Debit Card</title>
<link rel="stylesheet" href="https://fonts.googleapis.com/css2?family=Arimo:wght@700&family=Orbitron:wght@500;700&display=swap">
<style>
  :root {
    --page-bg: #ffffff;
    --card-black: #0b0b0b;
    --card-mid: #222222;
    --ink-white: #ffffff;
    --brand-orange: #f0902a;
    --watermark-grey: #333333;
    --emboss-shadow: #6b6b6b;
    --badge-ring: #f4f4f4;
  }
  html, body {
    margin: 0;
    width: 1200px;
    height: 1000px;
    overflow: hidden;
    background: var(--page-bg);
  }
  .canvas {
    position: relative;
    width: 1200px;
    height: 1000px;
  }
  .card {
    position: absolute;
    left: 75px;
    top: 162px;
    width: 1053px;
    height: 663px;
    border-radius: 22px;
    overflow: hidden;
    background: var(--card-black);
  }
  .card-texture {
    position: absolute;
    inset: 0;
    background:
      radial-gradient(ellipse 70% 55% at 30% 62%, var(--card-mid) 0%, rgba(34,34,34,0) 70%),
      linear-gradient(160deg, #101010 0%, #1b1b1b 45%, #090909 100%);
  }
  .brand {
    position: absolute;
    font-family: "Arimo", Arial, sans-serif;
    font-weight: 700;
    letter-spacing: 1px;
  }
  .brand-logo {
    left: 75px;
    top: 66px;
    font-size: 62px;
    color: var(--brand-orange);
  }
  .brand-underline {
    position: absolute;
    left: 63px;
    top: 133px;
    width: 364px;
    height: 9px;
    border-radius: 5px;
    background: var(--ink-white);
  }
  .watermark-mark {
    position: absolute;
    left: 305px;
    top: 170px;
    width: 170px;
    height: 170px;
    border-radius: 50%;
    background: var(--watermark-grey);
    opacity: 0.55;
  }
  .watermark-name {
    left: 575px;
    top: 198px;
    font-size: 92px;
    color: var(--watermark-grey);
    opacity: 0.8;
  }
  .card-number {
    position: absolute;
    top: 348px;
    font-family: "Orbitron", "Courier New", monospace;
    font-weight: 700;
    font-size: 42px;
    letter-spacing: 4px;
    color: var(--ink-white);
    text-shadow: 2px 3px 0 var(--emboss-shadow);
  }
  .group-1 { left: 73px; }
  .group-2 { left: 258px; }
  .group-3 { left: 462px; }
  .group-4 { left: 646px; }
  .card-code {
    position: absolute;
    left: 83px;
    top: 440px;
    font-family: "Orbitron", monospace;
    font-weight: 500;
    font-size: 17px;
    letter-spacing: 2px;
    color: var(--ink-white);
  }
  .valid-label {
    position: absolute;
    left: 521px;
    top: 440px;
    font-family: "Arimo", Arial, sans-serif;
    font-weight: 700;
    font-size: 17px;
    line-height: 22px;
    letter-spacing: 2px;
    text-align: center;
    color: var(--ink-white);
  }
  .valid-date {
    position: absolute;
    left: 618px;
    top: 452px;
    font-family: "Orbitron", monospace;
    font-weight: 700;
    font-size: 30px;
    letter-spacing: 3px;
    color: var(--ink-white);
    text-shadow: 2px 2px 0 var(--emboss-shadow);
  }
  .badge {
    position: absolute;
    left: 813px;
    width: 191px;
    height: 119px;
    border: 8px solid var(--badge-ring);
    border-radius: 64px;
    background: var(--card-black);
    display: flex;
    align-items: center;
    justify-content: center;
    gap: 10px;
  }
  .badge-issuer { top: 306px; }
  .badge-network { top: 491px; }
  .badge-dot {
    width: 22px;
    height: 22px;
    border-radius: 50%;
    background: var(--brand-orange);
  }
  .badge-name {
    font-family: "Arimo", Arial, sans-serif;
    font-weight: 700;
    font-size: 30px;
    color: var(--ink-white);
  }
  .debit-label {
    position: absolute;
    left: 813px;
    width: 207px;
    top: 444px;
    text-align: center;
    font-family: "Arimo", Arial, sans-serif;
    font-weight: 700;
    font-size: 40px;
    letter-spacing: 2px;
    color: var(--ink-white);
  }
</style>
</head>
<body>
<main class="canvas">
  <section class="card" aria-label="Toqavel prepaid debit card">
    <div class="card-texture" role="img" aria-label="Dark swirling light-streak texture across the card"></div>

    <div class="brand brand-logo">toqavel</div>
    <div class="brand-underline"></div>

    <div class="watermark-mark"></div>
    <div class="brand watermark-name">toqavel</div>

    <div class="card-number group-1">0000</div>
    <div class="card-number group-2">0000</div>
    <div class="card-number group-3">0000</div>
    <div class="card-number group-4">0000</div>

    <div class="card-code">0000</div>
    <div class="valid-label">VALID<br>THRU</div>
    <div class="valid-date">11/20</div>

    <div class="badge badge-issuer">
      <span class="badge-dot"></span>
      <span class="badge-name">toqavel</span>
    </div>
    <div class="debit-label">Debit</div>
    <div class="badge badge-network">
      <span class="badge-name">orbitpay</span>
    </div>
  </section>
</main>
</body>
</html>
```